Animal Eye Clinic needs a Business card

We are a new veterinary ophthalmology practice (Ridgeline Pet Vision Care) and we need a business card designed. We only see animal eyes - we are not a regular veterinary clinic. We already have a logo. We are looking for a professional, good looking business card to hand out to our clients. We are looking for something simple but professional and contemporary. Our logo is likely the only picture/graphic that needs to be on the card.
Updates

Contact Information for Business Card

Delia Vossman, BSc, DVM, MSc, DipACVO
Veterinary Ophthalmologist

Phone: 250.418.3927
Email: ridgelinepetvisioncare@mailbox-example.net
Website: ridgelinepetvisioncare-example.net
Address: 1874 Thornbury Rd
Kelowna, BC, V1X 4M9

Colors

Designer to choose colors to be used in the design.

Requirements
Must have
• Our logo (attached)

```html
<!DOCTYPE html>
<html lang="en">
<head>
<meta charset="utf-8">
<title>Ridgeline Pet Vision Care – Business Card</title>
<link href="https://fonts.googleapis.com/css2?family=Open+Sans:wght@400;600;700&display=swap" rel="stylesheet">
<style>
  :root {
    --teal: #0a97aa;
    --grey: #6f6f6f;
    --white: #ffffff;
    --backdrop: #8c8c8c;
  }
  * { box-sizing: border-box; margin: 0; padding: 0; }
  html, body {
    width: 1200px; height: 960px; overflow: hidden;
    background: var(--backdrop);
    font-family: "Open Sans", Arial, sans-serif;
  }
  .card {
    position: absolute;
    width: 680px; height: 389px;
    box-shadow: 0 10px 26px rgba(0,0,0,0.35);
    overflow: hidden;
  }
  .card--front { left: 80px; top: 60px; background: var(--white); }
  .card--back { left: 420px; top: 510px; background: var(--teal); }

  /* front */
  .brand {
    position: absolute; left: 0; right: 0; top: 140px;
    display: flex; align-items: center; justify-content: center; gap: 16px;
  }
  .brand__dot { width: 44px; height: 44px; border-radius: 50%; background: var(--teal); }
  .brand__name {
    color: var(--teal); font-weight: 700; font-size: 32px;
    letter-spacing: -0.5px;
  }
  .front__web {
    position: absolute; left: 0; right: 0; top: 290px;
    text-align: center; color: var(--grey);
    font-size: 15px; letter-spacing: 3px;
  }

  /* back */
  .back__art { position: absolute; inset: 0; }
  .person {
    position: absolute; left: 44px; top: 58px; color: var(--white);
    white-space: nowrap;
  }
  .person__name { font-size: 19px; font-weight: 700; }
  .person__creds { font-size: 11px; font-weight: 600; }
  .person__title { font-size: 15px; font-weight: 600; margin-top: 2px; }
  .contact {
    position: absolute; left: 44px; bottom: 34px; color: var(--white);
    font-size: 14px; line-height: 1.45; white-space: nowrap;
  }
  .contact__address { margin-bottom: 6px; }
  .contact__row { display: flex; align-items: center; gap: 9px; }
  .contact__icon { width: 13px; height: 13px; flex: none; }
</style>
</head>
<body>

<section class="card card--front" aria-label="Card front">
  <div class="brand">
    <span class="brand__dot"></span>
    <span class="brand__name">Ridgeline Pet Vision Care</span>
  </div>
  <p class="front__web">www.ridgelinepetvisioncare-example.net</p>
</section>

<section class="card card--back" aria-label="Card back">
  <svg class="back__art" width="680" height="389" viewBox="0 0 680 389">
    <path d="M405 0 H680 V389 H510 C430 340 385 250 385 160 C385 95 395 40 405 0 Z" fill="#ffffff"/>
    <circle cx="560" cy="170" r="130" fill="#0a97aa" role="img" aria-label="Large practice emblem area"/>
  </svg>

  <div class="person">
    <p class="person__name">Delia Vossman, <span class="person__creds">BSc, DVM, MSc, DipACVO</span></p>
    <p class="person__title">Veterinary Ophthalmologist</p>
  </div>

  <div class="contact">
    <p class="contact__address">1874 Thornbury Rd Kelowna,<br>BC, V1X 4M9</p>
    <p class="contact__row">
      <svg class="contact__icon" viewBox="0 0 16 16"><path d="M3 1h3l1.5 4-2 1.2a9 9 0 0 0 4.3 4.3L11 8.5l4 1.5v3a2 2 0 0 1-2 2A13 13 0 0 1 1 3a2 2 0 0 1 2-2z" fill="#fff"/></svg>
      250.418.3927
    </p>
    <p class="contact__row">
      <svg class="contact__icon" viewBox="0 0 16 16"><rect x="1" y="3" width="14" height="10" rx="1" fill="#fff"/><path d="M1.5 3.5 8 9l6.5-5.5" stroke="#0a97aa" stroke-width="1.4" fill="none"/></svg>
      ridgelinepetvisioncare@mailbox-example.net
    </p>
    <p class="contact__row">
      <svg class="contact__icon" viewBox="0 0 16 16"><circle cx="8" cy="8" r="7" fill="#fff"/><path d="M1 8h14M8 1c-3 3.5-3 10.5 0 14M8 1c3 3.5 3 10.5 0 14" stroke="#0a97aa" stroke-width="1.1" fill="none"/></svg>
      ridgelinepetvisioncare-example.net
    </p>
  </div>
</section>

</body>
</html>
```